Business Card Design for a Software Startup

We'd like to have a business card design. We already have a logo. Basically what we need is a clean design with name, address, cellphone and phone numbers, e-mail and web site address (front) and a space on the back with our logo with the company name on the right side and some texts on the bottom.
We are a development and consulting company in Brazil with highly qualified team of professionals in Java, iOS and Android development and consulting.

Target Market(s)

CIO, IT managers of mid to big size companies

Industry/Entity Type

Business

```html
<!DOCTYPE html>
<html lang="en">
<head>
<meta charset="utf-8">
<title>Veltro Business Cards</title>
<link rel="stylesheet" href="https://fonts.googleapis.com/css2?family=Source+Sans+3:wght@400;600;700&display=swap">
<style>
  :root {
    --bg: #e9e7e3;
    --card: #ffffff;
    --navy: #14335f;
    --blue: #1f5fa8;
    --blue-light: #3a7fd0;
    --blue-deep: #0f2a55;
    --ink: #3b3b3b;
    --rule: #c9c9c9;
  }
  * { box-sizing: border-box; margin: 0; padding: 0; }
  html, body { width: 1200px; height: 720px; overflow: hidden; }
  body {
    background: var(--bg);
    font-family: "Source Sans 3", sans-serif;
    color: var(--ink);
    position: relative;
  }
  .card {
    position: absolute;
    width: 540px;
    height: 308px;
    background: var(--card);
    box-shadow: 0 6px 18px rgba(0,0,0,0.12);
    overflow: hidden;
  }
  .card--front { left: 40px; top: 110px; }
  .card--back { left: 620px; top: 300px; }

  .front-band { position: absolute; inset: 0; width: 540px; height: 308px; }
  .holder {
    position: absolute; right: 22px; top: 12px; text-align: right; color: #fff;
  }
  .holder__name { font-size: 20px; font-weight: 700; line-height: 1.1; }
  .holder__title { font-size: 13px; font-weight: 400; }

  .brand { display: flex; align-items: center; gap: 12px; }
  .brand__mark { background: var(--blue); border-radius: 8px; }
  .brand__name { color: var(--navy); font-weight: 700; letter-spacing: 1px; line-height: 1; }

  .card--front .brand { position: absolute; left: 36px; top: 118px; }
  .card--front .brand__mark { width: 58px; height: 58px; }
  .card--front .brand__name { font-size: 62px; }

  .contact {
    position: absolute; left: 36px; top: 212px;
    list-style: none; font-size: 13px; line-height: 18px;
  }
  .contact li { display: flex; align-items: center; gap: 8px; }
  .contact svg { width: 11px; height: 11px; flex: none; }
  .divider {
    position: absolute; left: 198px; top: 214px; width: 1px; height: 40px; background: var(--rule);
  }
  .address {
    position: absolute; left: 212px; top: 210px; font-size: 13px; line-height: 17px; font-style: normal;
  }

  .card--back .brand {
    position: absolute; left: 0; right: 0; top: 56px;
    flex-direction: column; gap: 14px;
  }
  .card--back .brand__mark { width: 118px; height: 118px; border-radius: 14px; }
  .card--back .brand__name { font-size: 44px; }
  .site {
    position: absolute; left: 0; right: 0; bottom: 30px; text-align: center;
    font-size: 15px; letter-spacing: 5px; color: var(--ink);
  }
</style>
</head>
<body>

<section class="card card--front" aria-label="Business card front">
  <svg class="front-band" viewBox="0 0 540 308" aria-hidden="true">
    <defs>
      <linearGradient id="bandGrad" x1="0" y1="0" x2="1" y2="0">
        <stop offset="0" stop-color="#e4ecf6"/>
        <stop offset="0.45" stop-color="#3a7fd0"/>
        <stop offset="1" stop-color="#143a72"/>
      </linearGradient>
      <linearGradient id="foldGrad" x1="0" y1="0" x2="1" y2="1">
        <stop offset="0" stop-color="#1f5fa8"/>
        <stop offset="1" stop-color="#0f2a55"/>
      </linearGradient>
    </defs>
    <polygon points="190,0 540,0 540,58 300,74" fill="url(#bandGrad)"/>
    <path d="M300,74 L540,58 L540,128 C520,118 505,104 498,86 Z" fill="url(#foldGrad)"/>
  </svg>

  <div class="holder">
    <p class="holder__name">Your Name</p>
    <p class="holder__title">Title</p>
  </div>

  <div class="brand">
    <span class="brand__mark"></span>
    <span class="brand__name">VELTRO</span>
  </div>

  <ul class="contact">
    <li>
      <svg viewBox="0 0 12 12"><circle cx="6" cy="6" r="5.5" fill="none" stroke="#14335f"/><path d="M4 3.2l1 1.3-.6.8c.4.9 1 1.5 1.9 1.9l.8-.6 1.3 1-.6 1.1C5.8 8.6 3.4 6.2 3.3 4z" fill="#14335f"/></svg>
      555-210-4870
    </li>
    <li>
      <svg viewBox="0 0 12 12"><rect x="3.5" y="1" width="5" height="10" rx="1" fill="#14335f"/><rect x="4.4" y="2.2" width="3.2" height="6" fill="#fff"/></svg>
      555-318-2964
    </li>
    <li>
      <svg viewBox="0 0 12 12"><circle cx="6" cy="6" r="6" fill="#14335f"/><rect x="3" y="4" width="6" height="4" fill="#fff"/><path d="M3 4l3 2.2L9 4" fill="none" stroke="#14335f" stroke-width=".8"/></svg>
      yourname@veltro.com
    </li>
    <li>
      <svg viewBox="0 0 12 12"><circle cx="6" cy="6" r="5.3" fill="none" stroke="#14335f" stroke-width="1.2"/><ellipse cx="6" cy="6" rx="2.2" ry="5.3" fill="none" stroke="#14335f"/><path d="M0.7 6h10.6" stroke="#14335f"/></svg>
      www.veltro.com
    </li>
  </ul>

  <span class="divider"></span>

  <address class="address">
    Door No. Street Name<br>
    City Name, State, Zip Code
  </address>
</section>

<section class="card card--back" aria-label="Business card back">
  <div class="brand">
    <span class="brand__mark"></span>
    <span class="brand__name">VELTRO</span>
  </div>
  <p class="site">www.veltro.com</p>
</section>

</body>
</html>
```